Copper lark buildworks

Copper lark buildworks is a small construction company.
Who is a licenced builder, Carpenter, joiner,
working on heritage ,new build, speacial projects and sometimes furniture

Industry/Entity Type

Construction

```html
<!DOCTYPE html>
<html lang="en">
<head>
<meta charset="utf-8">
<title>Copper lark buildworks – business card</title>
<link rel="stylesheet" href="https://fonts.googleapis.com/css2?family=Open+Sans:wght@400;600&family=Roboto+Slab:wght@400&display=swap">
<style>
  :root {
    --stage: #5f5f5f;
    --paper: #ffffff;
    --green: #14a50a;
    --green-deep: #2d4a2a;
    --ink: #2f2f2f;
    --charcoal: #333333;
  }
  html, body {
    margin: 0;
    padding: 0;
    width: 1200px;
    height: 900px;
    overflow: hidden;
    background: var(--stage);
  }
  .stage {
    position: relative;
    width: 1200px;
    height: 900px;
  }
  .card {
    position: absolute;
    top: 306px;
    width: 439px;
    height: 272px;
    overflow: hidden;
  }
  .card--front { left: 149px; background: var(--paper); }
  .card--back {
    left: 610px;
    background:
      radial-gradient(ellipse 70% 75% at 48% 48%, var(--green) 0%, #14a00a 40%, rgba(20,160,10,0) 100%),
      linear-gradient(135deg, var(--green) 0%, var(--green) 45%, var(--green-deep) 100%);
    background-color: var(--green);
  }
  .card--back::before {
    content: "";
    position: absolute;
    inset: 0;
    background: radial-gradient(circle at 0% 100%, rgba(45,74,42,0.85) 0%, rgba(45,74,42,0) 35%);
  }
  .corner-mark { position: absolute; left: 0; top: 25px; }
  .holder {
    position: absolute;
    left: 37px;
    top: 24px;
    font-family: "Roboto Slab", serif;
  }
  .holder__name {
    margin: 0;
    font-size: 19px;
    font-weight: 400;
    color: var(--ink);
    line-height: 1.1;
  }
  .holder__first { color: var(--green); }
  .holder__role {
    margin: 3px 0 0;
    font-family: "Open Sans", sans-serif;
    font-size: 11.5px;
    color: var(--ink);
  }
  .company {
    position: absolute;
    font-family: "Roboto Slab", serif;
    font-weight: 400;
    color: var(--ink);
    display: flex;
    align-items: center;
    gap: 10px;
    white-space: nowrap;
  }
  .company__dot {
    width: 14px;
    height: 14px;
    background: var(--green);
    flex: none;
  }
  .card--front .company { left: 198px; top: 145px; font-size: 19px; }
  .card--back .company { left: 115px; top: 174px; font-size: 19px; z-index: 1; }
  .card--back .company__dot { background: var(--paper); }
  .contacts {
    position: absolute;
    left: 28px;
    top: 181px;
    margin: 0;
    padding: 0;
    list-style: none;
    font-family: "Open Sans", sans-serif;
    font-size: 11.5px;
    color: var(--ink);
    line-height: 15.8px;
  }
  .contacts li { display: flex; align-items: center; gap: 6px; }
  .contacts svg { width: 10px; height: 10px; flex: none; }
  .address {
    position: absolute;
    right: 26px;
    top: 211px;
    margin: 0;
    font-family: "Open Sans", sans-serif;
    font-style: normal;
    font-size: 11.5px;
    line-height: 16px;
    color: var(--ink);
    text-align: right;
  }
  .bottom-band { position: absolute; left: 0; bottom: 0; }
</style>
</head>
<body>
<main class="stage">

  <section class="card card--front" aria-label="Card front">
    <svg class="corner-mark" width="32" height="40" viewBox="0 0 32 40" aria-hidden="true">
      <polygon points="0,0 12,0 16,40 0,40" fill="var(--charcoal)"/>
      <polygon points="13,0 29,0 29,40 17,40" fill="var(--green)"/>
    </svg>

    <div class="holder">
      <h1 class="holder__name"><span class="holder__first">Harriet</span> Vale</h1>
      <p class="holder__role">Managing Director</p>
    </div>

    <div class="company">
      <span class="company__dot"></span>
      <span>Copper lark buildworks</span>
    </div>

    <ul class="contacts">
      <li>
        <svg viewBox="0 0 10 10" aria-hidden="true"><rect x="2.5" y="0" width="5" height="10" rx="1" fill="var(--green)"/><rect x="3.5" y="1.5" width="3" height="6" fill="#fff"/></svg>
        044-555 201 774
      </li>
      <li>
        <svg viewBox="0 0 10 10" aria-hidden="true"><path d="M0 3 Q5 0 10 3 L9 4.5 L7 4 L7 3 Q5 2 3 3 L3 4 L1 4.5Z" fill="var(--green)"/><rect x="1.5" y="5" width="7" height="5" rx="1" fill="var(--green)"/></svg>
        044-555 201 774
      </li>
      <li>
        <svg viewBox="0 0 10 10" aria-hidden="true"><rect x="0" y="1.5" width="10" height="7" fill="var(--green)"/><polyline points="0.5,2 5,5.5 9.5,2" fill="none" stroke="#fff" stroke-width="1"/></svg>
        info@copperlark.com
      </li>
      <li>
        <svg viewBox="0 0 10 10" aria-hidden="true"><circle cx="5" cy="5" r="5" fill="var(--green)"/><path d="M2 3 Q4 4 3 6 Q5 7 4 9 M7 1.5 Q6 4 8 5" fill="none" stroke="#fff" stroke-width="1"/></svg>
        www.copperlarkbuild.com
      </li>
    </ul>

    <address class="address">18 Wren Lane, Harlow Mill<br>Eastshire, 40217.</address>

    <svg class="bottom-band" width="439" height="15" viewBox="0 0 439 15" aria-hidden="true">
      <polygon points="0,0 216,0 206,15 0,15" fill="var(--charcoal)"/>
      <polygon points="221,0 439,0 439,15 209,15" fill="var(--green)"/>
    </svg>
  </section>

  <section class="card card--back" aria-label="Card back">
    <div class="company">
      <span class="company__dot"></span>
      <span>Copper lark buildworks</span>
    </div>
  </section>

</main>
</body>
</html>
```